Business card for denture clinic Veltrimora

We need a new business card with our new logo. We are a denture clinic in New Zealand with our target market being 45+ years old. We would need a space on the back to write our patients next appointment on. We would space for only one appointment rather than a list. We will attach a photo showing an example of this. But of course, we would like to see your twist on this. We want it to be bold and easy to read and a good mixture of professional but modern. We have attached our logo to be used on the card.

Target Market(s)

People aged 45+ needing dentures

Industry/Entity Type

Dental

Contact Information for Business Card

We want our logo on the front and the space to write an appointment on the back. I've attached an example our our old business card showing this. We need to have the technicians details on the front.

Font styles to use
Sans Serif

Colors
0255a3
919191
fbfbfb

Requirements
Must have
• The following details:
• Liam Dorsett BDT, PGDipCDentTech Calverin
• Dental Prosthetist
• Phone numbers: 0800 47 3125
• 09 572 1394
• Email: liam@veltrimora.co.nz
• www.veltrimora.co.nz
• Address: 14 Marlow Crest Road
• Halbrook West
• Auckland 0793
Nice to have
• We would like our business cards to have more than just two colours as we want them to be more vibrant. We have uploaded an example of a business card we liked that showed this.

```html
<!DOCTYPE html>
<html lang="en">
<head>
<meta charset="utf-8">
<title>Veltrimora Business Card</title>
<link rel="stylesheet" href="https://fonts.googleapis.com/css2?family=Lato:ital,wght@0,400;0,700;0,900;1,400&display=swap">
<style>
  :root {
    --brand-blue: #0260a3;
    --brand-blue-dark: #0255a3;
    --brand-accent: #29a3dc;
    --brand-grey: #919191;
    --card-white: #fbfbfb;
    --ink: #1e1e1e;
    --page: #ececec;
    --white: #ffffff;
  }
  * { box-sizing: border-box; margin: 0; padding: 0; }
  html, body {
    width: 1200px; height: 586px; overflow: hidden;
    background: var(--page);
    font-family: "Lato", sans-serif;
  }
  .canvas { position: relative; width: 1200px; height: 586px; }
  .card {
    position: absolute; top: 129px;
    width: 502px; height: 301px;
    overflow: hidden;
  }

  /* Back: appointment side */
  .card-back { left: 61px; background: var(--brand-blue); color: var(--white); }
  .appointment-title {
    position: absolute; top: 69px; left: 0; width: 100%;
    text-align: center; font-weight: 700; font-size: 14px;
    letter-spacing: 3.6px;
  }
  .appointment-title span {
    border-bottom: 1.5px solid var(--accent-line, var(--white)); padding: 0 0 1px 3px;
  }
  .field-label {
    position: absolute; top: 117px; font-size: 13px; font-weight: 400;
  }
  .field-box {
    position: absolute; top: 141px; width: 204px; height: 33px;
    background: var(--white); border-radius: 4px;
  }
  .field-date { left: 36px; }
  .field-time { left: 263px; }
  .hours-title {
    position: absolute; top: 244px; left: 0; width: 100%;
    text-align: center; font-size: 12.5px; font-weight: 700;
  }
  .hours-title span { border-bottom: 1px solid var(--white); }
  .hours-line {
    position: absolute; top: 268px; left: 0; width: 100%;
    text-align: center; font-size: 12.5px;
  }
  .hours-line b { font-weight: 700; }
  .hours-line .sep { margin: 0 5px; color: var(--brand-accent); }

  /* Front: contact side */
  .card-front { left: 619px; background: var(--card-white); color: var(--ink); }
  .brand-mark {
    position: absolute; top: 28px; left: 222px;
    width: 40px; height: 40px; background: var(--brand-blue); border-radius: 2px;
  }
  .brand-name {
    position: absolute; top: 69px; left: 0; width: 484px;
    text-align: center; font-size: 21px; font-weight: 700;
    letter-spacing: 1px; color: var(--brand-blue);
  }
  .technician {
    position: absolute; top: 156px; right: 277px; text-align: right;
  }
  .technician-name { font-size: 16px; font-weight: 700; color: var(--brand-blue); }
  .technician-credentials { margin-top: 3px; font-size: 10.5px; font-style: italic; color: var(--brand-grey); }
  .technician-role { margin-top: 19px; font-size: 11px; font-weight: 700; }
  .divider {
    position: absolute; left: 231px; top: 139px; width: 2px; height: 118px;
    background: linear-gradient(to bottom, rgba(41,163,220,0), var(--brand-accent) 30%, var(--brand-blue) 60%, rgba(2,96,163,0));
  }
  .contact-list { position: absolute; top: 155px; left: 258px; list-style: none; }
  .contact-item {
    display: flex; align-items: center; height: 24px;
    font-size: 12px;
  }
  .contact-web { color: var(--brand-blue); font-weight: 700; }
  .contact-icon { width: 17px; height: 17px; margin-right: 7px; flex: none; }
  .address-band {
    position: absolute; left: 0; bottom: 0; width: 100%; height: 25px;
    background: var(--brand-blue); color: var(--white);
    border-top: 3px solid var(--brand-accent);
    text-align: center; font-size: 12.5px; font-weight: 700; line-height: 22px;
  }
</style>
</head>
<body>
<main class="canvas">

  <section class="card card-back" aria-label="Appointment card">
    <h2 class="appointment-title"><span>Your Next Appointment</span></h2>
    <p class="field-label" style="left:36px">Date:</p>
    <div class="field-box field-date"></div>
    <p class="field-label" style="left:263px">Time:</p>
    <div class="field-box field-time"></div>
    <p class="hours-title"><span>Opening Hours</span></p>
    <p class="hours-line"><b>Mon - Thurs:</b> 9.00am - 5.00pm<span class="sep">|</span><b>Fri - Sat:</b> 9.00am - 1.00pm</p>
  </section>

  <section class="card card-front" aria-label="Contact card">
    <div class="brand-mark"></div>
    <h1 class="brand-name">VELTRIMORA</h1>

    <div class="technician">
      <p class="technician-name">Liam Dorsett BDT</p>
      <p class="technician-credentials">PGDipCDentTech Calverin</p>
      <p class="technician-role">Dental Prosthetist</p>
    </div>

    <div class="divider"></div>

    <ul class="contact-list">
      <li class="contact-item">
        <svg class="contact-icon" viewBox="0 0 20 20" aria-hidden="true"><circle cx="10" cy="10" r="10" fill="#0260a3"/><path d="M5 8.5c0-1.6 2.2-2.6 5-2.6s5 1 5 2.6l-1.8.6-.6-1.3H7.4l-.6 1.3zM6.5 9.5h7l1 4.3h-9z" fill="#fff"/></svg>
        0800 47 3125
      </li>
      <li class="contact-item">
        <svg class="contact-icon" viewBox="0 0 20 20" aria-hidden="true"><circle cx="10" cy="10" r="10" fill="#0260a3"/><path d="M5 8.5c0-1.6 2.2-2.6 5-2.6s5 1 5 2.6l-1.8.6-.6-1.3H7.4l-.6 1.3zM6.5 9.5h7l1 4.3h-9z" fill="#fff"/></svg>
        09 572 1394
      </li>
      <li class="contact-item">
        <svg class="contact-icon" viewBox="0 0 20 20" aria-hidden="true"><circle cx="10" cy="10" r="10" fill="#0260a3"/><rect x="5" y="6.5" width="10" height="7" fill="none" stroke="#fff" stroke-width="1.2"/><path d="M5 6.5l5 4 5-4" fill="none" stroke="#fff" stroke-width="1.2"/></svg>
        liam@veltrimora.co.nz
      </li>
      <li class="contact-item contact-web">
        <svg class="contact-icon" viewBox="0 0 20 20" aria-hidden="true"><circle cx="10" cy="10" r="10" fill="#29a3dc"/><circle cx="10" cy="10" r="5" fill="none" stroke="#fff" stroke-width="1.2"/><ellipse cx="10" cy="10" rx="2.2" ry="5" fill="none" stroke="#fff" stroke-width="1"/><path d="M5 10h10" stroke="#fff" stroke-width="1"/></svg>
        www.veltrimora.co.nz
      </li>
    </ul>

    <p class="address-band">14 Marlow Crest Road, Halbrook West Auckland 0793</p>
  </section>

</main>
</body>
</html>
```